Agarwood Oud Label Design

I need a circular product label designed for an Agarwood or Bakhoor product. I will provide a rich color scheme picture, as well as the company logo. It may be easier to play with different angles of the logo. So, they are attached also. Label should be 56mm diameter circle label.

```html
<!DOCTYPE html>
<html lang="en">
<head>
<meta charset="utf-8">
<title>Agarwood Oudh Label</title>
<link href="https://fonts.googleapis.com/css2?family=Cormorant+Garamond:ital,wght@0,600;1,700&family=Noto+Nastaliq+Urdu:wght@700&family=Roboto+Condensed:wght@700&display=swap" rel="stylesheet">
<style>
  :root {
    --page-black: #000000;
    --page-edge: #d9d9d9;
    --band-brown: #4a1512;
    --band-deep: #2e0b09;
    --gold-light: #fbe38a;
    --gold-mid: #e0ae35;
    --gold-dark: #9a6512;
    --maroon: #8e1517;
    --maroon-deep: #5a0c0e;
    --ink-dark: #2a0d06;
    --cream: #f6ead4;
  }
  html, body {
    margin: 0;
    padding: 0;
    width: 1200px;
    height: 1200px;
    overflow: hidden;
    background: var(--page-black);
  }
  .label-canvas {
    position: relative;
    width: 1200px;
    height: 1200px;
    box-sizing: border-box;
    border: 3px solid var(--page-edge);
    background: var(--page-black);
  }
  .label-art {
    position: absolute;
    inset: 0;
  }
  .brand-plate {
    position: absolute;
    left: 462px;
    top: 254px;
    width: 264px;
    height: 112px;
    display: flex;
    align-items: center;
    justify-content: center;
    font-family: "Cormorant Garamond", serif;
    font-weight: 600;
    font-size: 36px;
    color: var(--cream);
    letter-spacing: 0.5px;
  }
  .urdu-name {
    position: absolute;
    left: 0;
    width: 1200px;
    top: 548px;
    text-align: center;
    font-family: "Noto Nastaliq Urdu", serif;
    font-weight: 700;
    font-size: 30px;
    line-height: 70px;
    color: var(--gold-light);
    direction: rtl;
  }
  .product-title {
    position: absolute;
    left: 0;
    width: 1200px;
    text-align: center;
    font-family: "Cormorant Garamond", serif;
    font-style: italic;
    font-weight: 700;
    line-height: 1;
    background: linear-gradient(180deg, var(--gold-light) 0%, var(--gold-mid) 55%, var(--gold-dark) 100%);
    -webkit-background-clip: text;
    background-clip: text;
    color: transparent;
    filter: drop-shadow(2px 3px 2px rgba(0,0,0,0.7));
  }
  .title-line-one { top: 610px; font-size: 104px; letter-spacing: 10px; }
  .title-line-two { top: 705px; font-size: 100px; letter-spacing: 4px; }
  .weight-text {
    position: absolute;
    left: 0;
    width: 1200px;
    top: 846px;
    text-align: center;
    font-family: "Roboto Condensed", sans-serif;
    font-weight: 700;
    font-size: 42px;
    line-height: 50px;
    color: var(--ink-dark);
  }
</style>
</head>
<body>
<div class="label-canvas">
  <svg class="label-art" width="1200" height="1200" viewBox="0 0 1200 1200">
    <defs>
      <radialGradient id="scene-tone" cx="50%" cy="45%" r="60%">
        <stop offset="0%" stop-color="#6e2218"/>
        <stop offset="55%" stop-color="#4a140f"/>
        <stop offset="100%" stop-color="#240807"/>
      </radialGradient>
      <linearGradient id="gold-ring" x1="0" y1="0" x2="1" y2="1">
        <stop offset="0%" stop-color="#fbe38a"/>
        <stop offset="50%" stop-color="#e0ae35"/>
        <stop offset="100%" stop-color="#9a6512"/>
      </linearGradient>
      <linearGradient id="gold-pill" x1="0" y1="0" x2="0" y2="1">
        <stop offset="0%" stop-color="#fff6c8"/>
        <stop offset="50%" stop-color="#e9c04d"/>
        <stop offset="100%" stop-color="#b07a18"/>
      </linearGradient>
    </defs>

    <g class="outer-band">
      <circle cx="600" cy="598" r="436" fill="var(--band-deep)"/>
      <circle cx="600" cy="598" r="428" fill="var(--band-brown)" role="img" aria-label="Gold geometric knot pattern band around the label"/>
      <circle cx="600" cy="598" r="428" fill="none" stroke="var(--gold-dark)" stroke-width="2"/>
      <circle cx="600" cy="598" r="378" fill="var(--band-deep)"/>
    </g>

    <circle class="gold-frame" cx="600" cy="598" r="372" fill="url(#gold-ring)"/>

    <circle class="product-scene" cx="600" cy="598" r="362" fill="url(#scene-tone)" role="img" aria-label="Photo of an antique silver-capped perfume bottle, ornate metal incense boxes and agarwood chips on red cloth"/>

    <g class="brand-oval">
      <ellipse cx="594" cy="310" rx="136" ry="58" fill="url(#gold-ring)"/>
      <ellipse cx="594" cy="310" rx="128" ry="51" fill="var(--maroon)"/>
    </g>

    <g class="urdu-ornaments">
      <ellipse cx="440" cy="584" rx="30" ry="18" fill="var(--gold-mid)" role="img" aria-label="Small gold flourish ornament"/>
      <ellipse cx="768" cy="584" rx="30" ry="18" fill="var(--gold-mid)" role="img" aria-label="Small gold flourish ornament"/>
    </g>

    <g class="weight-badge">
      <rect x="458" y="815" width="284" height="112" rx="56" fill="url(#gold-ring)"/>
      <rect x="464" y="821" width="272" height="100" rx="50" fill="var(--maroon-deep)" role="img" aria-label="Gold filigree ornament on maroon badge"/>
      <rect x="490" y="838" width="220" height="66" rx="33" fill="url(#gold-pill)" stroke="var(--gold-dark)" stroke-width="2"/>
    </g>
  </svg>

  <div class="brand-plate">Amber &amp; Ember</div>
  <div class="urdu-name">اگرووڈ عود</div>
  <div class="product-title title-line-one">Agarwood</div>
  <div class="product-title title-line-two">Oudh</div>
  <div class="weight-text">50 grams</div>
</div>
</body>
</html>
```